Vantoq Business Card Project showing the logo and a marbo image on the rear

Design a whacky but professional business card, the logo is for the front and the Marbo image is for the rear. Happy to consider other open source Marbo Images if the designer wants to select one from the web. Vantoq is a competitor to OMB.com.au and Pellory.com.au and is based around every property in Australia

Target Market(s)

Business

Contact Information for Business Card

Name, Title, Email, Web, Phone Number

Font styles to use
Other font styles liked:
• avenir

Requirements
Must have
• Image on Back logo on front
Nice to have
• Happy to consider other images on rear, preftably Colin Marbo. Image supplied I own, we can use open source other Marbo Images

```html
<!DOCTYPE html>
<html lang="en">
<head>
<meta charset="utf-8">
<title>Vantoq Business Card</title>
<link href="https://fonts.googleapis.com/css2?family=Jost:wght@500;600&family=Roboto:wght@400&display=swap" rel="stylesheet">
<style>
  :root {
    --backdrop: #2a2a2b;
    --card-white: #f1f1f0;
    --ink: #1b1b1b;
    --brand-orange: #ea8410;
    --night: #3a3d42;
    --town-pink: #e0449a;
    --town-yellow: #e8e23a;
    --town-blue: #3f9fd8;
    --grass: #7cc234;
  }
  * { box-sizing: border-box; margin: 0; padding: 0; }
  html, body {
    width: 1138px; height: 1200px; overflow: hidden;
    background: var(--backdrop);
  }
  .canvas { position: relative; width: 1138px; height: 1200px; }

  .card {
    position: absolute;
    width: 375px; height: 620px;
    border-radius: 14px;
    overflow: hidden;
  }
  .card--rear { left: 156px; top: 276px; }
  .card--front { left: 577px; top: 274px; background: var(--card-white); }

  .rear-artwork {
    width: 100%; height: 100%;
    background:
      linear-gradient(180deg, rgba(0,0,0,0) 0 62%, var(--town-pink) 74%, var(--town-yellow) 88%, var(--grass) 96%),
      linear-gradient(90deg, var(--brand-orange) 0 50%, var(--night) 50% 100%);
  }

  .brand {
    position: absolute; left: 0; right: 0; top: 56px;
    display: flex; align-items: center; justify-content: center; gap: 14px;
  }
  .brand-mark {
    width: 54px; height: 54px; background: var(--brand-orange);
  }
  .brand-name {
    font-family: 'Jost', sans-serif; font-weight: 600;
    font-size: 66px; line-height: 1; color: var(--ink);
    letter-spacing: 1px;
  }

  .person { position: absolute; left: 0; right: 0; top: 184px; text-align: center; }
  .person-name {
    font-family: 'Jost', sans-serif; font-weight: 600;
    font-size: 25px; color: var(--ink); line-height: 28px;
  }
  .person-title {
    font-family: 'Roboto', sans-serif; font-size: 16px;
    color: var(--brand-orange); margin-top: 3px;
  }

  .divider {
    position: absolute; left: 57px; right: 57px; top: 265px;
    display: flex; align-items: center; gap: 8px;
  }
  .divider-line { flex: 1; height: 2px; background: var(--brand-orange); }
  .divider-icons { display: flex; gap: 3px; }
  .icon-badge {
    width: 27px; height: 27px; border-radius: 50%;
    border: 1.5px solid var(--brand-orange);
    display: flex; align-items: center; justify-content: center;
  }
  .icon-badge svg { width: 14px; height: 14px; }

  .contact {
    position: absolute; left: 0; right: 0; top: 302px;
    text-align: center;
    font-family: 'Roboto', sans-serif; font-size: 16px; line-height: 24px;
    color: var(--ink);
  }
  .address {
    position: absolute; left: 0; right: 0; top: 400px;
    text-align: center;
    font-family: 'Roboto', sans-serif; font-size: 16px; color: var(--ink);
  }

  .front-artwork {
    position: absolute; left: 0; right: 0; bottom: 0; height: 172px;
    background: linear-gradient(180deg, var(--card-white) 0%, var(--town-pink) 22%, var(--town-blue) 48%, var(--town-yellow) 80%, var(--grass) 92%);
  }
</style>
</head>
<body>
<main class="canvas">
  <section class="card card--rear">
    <div class="rear-artwork" role="img" aria-label="Colourful cartoon city illustration: day sky with sun and clouds on the left, night sky with stars and a plane on the right, above a row of smiling buildings and a train"></div>
  </section>

  <section class="card card--front">
    <div class="brand">
      <span class="brand-mark"></span>
      <span class="brand-name">Vantoq</span>
    </div>

    <div class="person">
      <div class="person-name">Owen Tarrick</div>
      <div class="person-title">Founder &amp; CEO</div>
    </div>

    <div class="divider">
      <span class="divider-line"></span>
      <div class="divider-icons">
        <span class="icon-badge">
          <svg viewBox="0 0 16 16" fill="none" stroke="#ea8410" stroke-width="1.6" stroke-linejoin="round">
            <path d="M3 3h3l1.2 3-1.7 1.1a8 8 0 0 0 3.4 3.4L10 8.8 13 10v3a1 1 0 0 1-1 1A11 11 0 0 1 2 4a1 1 0 0 1 1-1z"/>
          </svg>
        </span>
        <span class="icon-badge">
          <svg viewBox="0 0 16 16" fill="none" stroke="#ea8410" stroke-width="1.6" stroke-linejoin="round">
            <rect x="2" y="4" width="12" height="9"/><path d="M2 4l6 5 6-5"/>
          </svg>
        </span>
        <span class="icon-badge">
          <svg viewBox="0 0 16 16" fill="none" stroke="#ea8410" stroke-width="1.4">
            <circle cx="8" cy="8" r="6"/><ellipse cx="8" cy="8" rx="2.6" ry="6"/><path d="M2 8h12"/>
          </svg>
        </span>
      </div>
      <span class="divider-line"></span>
    </div>

    <div class="contact">
      <div>(00) 4444 5555</div>
      <div>tarrick@vantoq.com</div>
      <div>www.vantoq.com</div>
    </div>

    <div class="address">Level 4, 18 Calder Lane, Sydney 2000, AU</div>

    <div class="front-artwork" role="img" aria-label="Colourful cartoon skyline of smiling buildings with a train running along the bottom"></div>
  </section>
</main>
</body>
</html>
```